Website Design Project for Beauty & Wellness Professionals

As background information, I have a website that is focused on Beauty & Wellness Professionals:
- Job Search (www.lumarinovo.com)
- Business Classifieds (negocios.lumarinovo.com)
- Freelancer Classifieds (freelancer.lumarinovo.com)
- Course Reviews (cursos.lumarinovo.com)

All those websites use standard templates.

I need a DESIGN for the HOME PAGE (no coding) of the Website Platform that consolidates the four platforms under the same design.

Website designs that we like:
- quelvox.com
- brintmoor.com

Target Market(s)

Brazilian Professionals from Beauty & Wellness sector

Industry/Entity Type

Business

Requirements
Must have
• Website designs that we like:
- quelvox.com
- brintmoor.com

```html
<!DOCTYPE html>
<html lang="en">
<head>
<meta charset="utf-8">
<title>Lumarinovo – Home</title>
<link rel="stylesheet" href="https://fonts.googleapis.com/css2?family=Archivo+Black&family=Open+Sans:wght@400;600;700;800&family=Roboto:wght@400;700;900&display=swap">
<style>
:root{
  --white:#ffffff;
  --ink:#2b2b2b;
  --muted:#6f6f6f;
  --teal:#4aa3b5;
  --accent:#c0502a;
  --red:#e8321c;
  --beige:#ebe3d7;
  --green:#5f9a5c;
  --blue:#5ea7bf;
  --footer:#2a2a2a;
  --rule:#e2e2e2;
}
*{margin:0;padding:0;box-sizing:border-box}
html,body{width:765px;height:1200px;overflow:hidden;background:var(--white)}
body{position:relative;font-family:"Open Sans",Arial,sans-serif;color:var(--ink)}
.abs{position:absolute}

/* header */
.brand{left:90px;top:12px;display:flex;align-items:center;gap:10px}
.brand-dot{width:36px;height:36px;border-radius:50%;background:var(--teal)}
.brand-name{font-family:"Roboto",Arial,sans-serif;font-size:22px;color:var(--teal);font-weight:400}
.nav a{position:absolute;top:27px;font-family:"Roboto",Arial,sans-serif;font-size:10.5px;color:#222;text-decoration:none;white-space:nowrap}
.nav a.current{color:var(--accent)}

/* hero */
.hero{left:0;top:58px;width:765px;height:253px;background:linear-gradient(90deg,#3c4a44 0%,#4e5a52 20%,#2f3530 45%,#141414 75%,#0d0d0d 100%)}
.hero-portrait{left:170px;top:58px;width:190px;height:253px;background:radial-gradient(ellipse at 45% 40%,#d78a5e 0%,#a64a2a 35%,rgba(60,70,65,0) 75%)}
.hero-ornament{left:560px;top:70px;width:180px;height:200px;background:radial-gradient(ellipse,rgba(90,90,90,.35),rgba(20,20,20,0) 70%)}
.hero-title{font-family:"Open Sans",Arial,sans-serif;font-weight:700;white-space:nowrap;line-height:1}
.t-beautiful{left:320px;top:127px;font-size:35px;color:var(--white)}
.t-permanent{left:338px;top:178px;font-size:26px;color:#a4a4a4;font-weight:600}
.t-makeup{left:342px;top:203px;font-size:56px;color:var(--red)}
.t-services{left:482px;top:260px;font-size:18px;color:rgba(140,190,140,.55)}
.book-label{left:88px;top:243px;font-size:12.5px;color:var(--white);font-family:"Roboto",Arial,sans-serif}

.booking{left:88px;top:262px;width:588px;height:48px;background:rgba(95,154,92,.85);border:2px solid rgba(150,200,140,.7)}
.field{position:absolute;top:12px;height:22px;background:var(--white);border:1px solid #bbb;font-size:8.5px;color:#444;padding:5px 6px}
.submit{position:absolute;top:12px;left:542px;width:37px;height:22px;background:#111;color:#fff;border:1px solid #ddd;font-size:9.5px;text-align:center;line-height:20px}

/* features */
.features{left:88px;top:311px;width:588px;height:144px;background:var(--beige)}
.feature{position:absolute;top:17px;width:180px}
.feature-photo{position:absolute;left:0;top:0;width:64px;height:64px;border-radius:50%;background:radial-gradient(circle,#e8c8a8,#a88060);border:2px solid #fff}
.feature h3{position:absolute;left:76px;top:-1px;font-family:"Roboto",Arial,sans-serif;font-size:18px;line-height:17px;font-weight:700;color:#333}
.feature p{position:absolute;left:76px;top:43px;width:100px;font-size:8.5px;line-height:12px;color:#8a8a8a}
.read-more{position:absolute;left:76px;top:96px;width:54px;height:14px;background:#fff;border:1px solid #ddd;border-radius:2px;font-size:6px;color:#555;text-align:center;line-height:12px}

/* mid */
.h-welcome{left:90px;top:484px;font-family:"Archivo Black",Arial,sans-serif;font-size:22px;color:#1c1c1c}
.h-sec{font-family:"Roboto",Arial,sans-serif;font-weight:900;font-size:14.5px;color:#1c1c1c;line-height:17px;letter-spacing:.3px}
.frame{left:88px;top:520px;width:189px;height:82px;border:1px solid #ddd;background:#fff}
.photo{background:linear-gradient(135deg,#c9a7a0,#7f6a78)}
.small-text{font-size:8.5px;line-height:10.5px;color:#555}
.small-text a{color:var(--accent)}
.caption{font-family:"Roboto",Arial,sans-serif;font-size:10px;color:#333;text-align:center}
.pop{font-family:"Roboto",Arial,sans-serif;font-size:11px;color:#333;list-style:none}
.pop li{position:absolute;white-space:nowrap;padding-left:12px}
.pop li::before{content:"";position:absolute;left:0;top:3px;border-left:4px solid var(--accent);border-top:3px solid transparent;border-bottom:3px solid transparent}
.rule{left:88px;top:658px;width:588px;height:1px;background:var(--rule)}

.col-photo{position:absolute;top:701px;width:175px;height:106px}
.col-text{position:absolute;top:820px;width:175px;font-size:8.5px;line-height:13px;color:#555}
.checks{list-style:none}
.checks li{position:relative;padding-left:11px;margin-bottom:8px}
.checks li::before{content:"";position:absolute;left:0;top:3px;border-left:4px solid #222;border-top:3px solid transparent;border-bottom:3px solid transparent}
.more{position:absolute;top:912px;width:45px;height:25px;background:var(--blue);color:#fff;font-size:10.5px;text-align:center;line-height:25px;border-radius:2px}

/* links */
.h-links{left:88px;top:957px;font-family:"Roboto",Arial,sans-serif;font-size:14px;color:#333}
.card{position:absolute;top:989px;width:135px;height:108px;border-radius:8px;overflow:hidden}
.card-band{position:absolute;left:0;top:0;width:100%;height:36px;background:rgba(70,70,70,.8)}
.card-title{position:absolute;left:0;top:5px;width:100%;text-align:center;font-family:"Roboto",Arial,sans-serif;font-weight:900;font-size:12.5px;line-height:14px;color:#fff;letter-spacing:.3px}
.click{position:absolute;top:1105px;width:135px;text-align:center;font-family:"Roboto",Arial,sans-serif;font-size:10px;color:#444;text-decoration:underline}

/* footer */
.footer{left:0;top:1133px;width:765px;height:67px;background:var(--footer)}
.foot-nav{position:absolute;top:1154px;font-family:"Roboto",Arial,sans-serif;font-size:9px;color:#ccc;white-space:nowrap}
.copyright{left:88px;top:1173px;font-size:7.5px;color:#777}
.social{position:absolute;top:1150px;width:19px;height:19px;border-radius:50%;background:#8a8a8a}
</style>
</head>
<body>

<header>
  <div class="abs brand"><span class="brand-dot"></span><span class="brand-name">Lumarinovo</span></div>
  <nav class="nav">
    <a class="current" style="left:342px">HOME</a>
    <a style="left:396px">ABOUT US</a>
    <a style="left:471px">SERVICES</a>
    <a style="left:547px">GALLERY</a>
    <a style="left:614px">CONTACT US</a>
  </nav>
</header>

<section>
  <div class="abs hero" role="img" aria-label="Hero photo: model with red hair and dramatic makeup over a dark ornamental background"></div>
  <div class="abs hero-portrait" aria-hidden="true"></div>
  <div class="abs hero-ornament" aria-hidden="true"></div>
  <div class="abs hero-title t-beautiful">BEAUTIFUL</div>
  <div class="abs hero-title t-permanent">PERMANENT</div>
  <div class="abs hero-title t-makeup">MAKEUP</div>
  <div class="abs hero-title t-services">SERVICES</div>
  <div class="abs book-label">BOOK YOUR APPOINTMENT</div>
  <form class="abs booking">
    <div class="field" style="left:7px;width:130px">Stylist:</div>
    <div class="field" style="left:141px;width:129px">Date:</div>
    <div class="field" style="left:275px;width:129px">Time:</div>
    <div class="field" style="left:409px;width:129px">Salon:</div>
    <div class="submit">Submit</div>
  </form>
</section>

<section class="abs features">
  <div class="feature" style="left:17px">
    <div class="feature-photo" role="img" aria-label="Bride with flower in hair"></div>
    <h3>Bridal<br>services</h3>
    <p>Lorem ipsum dolor sit amet consectetuer adipi scing elraesent</p>
    <div class="read-more">Read More</div>
  </div>
  <div class="feature" style="left:206px">
    <div class="feature-photo" role="img" aria-label="Spa candles and oils" style="background:radial-gradient(circle,#e0b860,#6a5030)"></div>
    <h3>Spa<br>services</h3>
    <p>Consectetuer adipicing elraesent ves tiacean nonuhendrerit</p>
    <div class="read-more">Read More</div>
  </div>
  <div class="feature" style="left:394px">
    <div class="feature-photo" role="img" aria-label="Facial treatment" style="background:radial-gradient(circle,#f0e0d0,#b09a80)"></div>
    <h3>Facial &amp;<br>skin care</h3>
    <p>Aenean nonum endrerit mauris. Phase llusrce suscipit vius mi</p>
    <div class="read-more">Read More</div>
  </div>
</section>

<section>
  <h2 class="abs h-welcome">WELCOME</h2>
  <div class="abs frame"><div class="abs photo" style="left:6px;top:6px;width:175px;height:68px" role="img" aria-label="Close-up of eye with pink eye makeup"></div></div>
  <p class="abs small-text" style="left:88px;top:612px;width:190px">Nulla ut tempus quam. Aenean augue eros, placerat quis interdum eu, varius vel urna. Fusce vitae posuere nulla, a pellentesque mi. <a>Learn more</a></p>

  <h2 class="abs h-sec" style="left:307px;top:488px">VIDEO GALLERY</h2>
  <div class="abs photo" style="left:307px;top:520px;width:74px;height:88px;background:linear-gradient(160deg,#e8e0d8,#b09080)" role="img" aria-label="Video: facial mask treatment"></div>
  <div class="abs photo" style="left:390px;top:520px;width:74px;height:88px;background:linear-gradient(160deg,#d8b098,#8a5040)" role="img" aria-label="Video: massage"></div>
  <div class="abs caption" style="left:307px;top:619px;width:74px">SPACIAL CARE</div>
  <div class="abs caption" style="left:390px;top:618px;width:74px">MASSAGE</div>

  <h2 class="abs h-sec" style="left:493px;top:488px">MOST POPULAR<br>SERVICES</h2>
  <ul class="pop">
    <li class="abs" style="left:495px;top:534px">MANICURE</li>
    <li class="abs" style="left:495px;top:555px">MAKE-UP</li>
    <li class="abs" style="left:495px;top:576px">PEDICURE</li>
    <li class="abs" style="left:584px;top:534px">SKIN CARE</li>
    <li class="abs" style="left:584px;top:555px">HAIR DESIGN</li>
    <li class="abs" style="left:584px;top:576px">PARAFFIN WAX</li>
  </ul>
  <div class="abs rule"></div>
</section>

<section>
  <h2 class="abs h-sec" style="left:88px;top:671px;font-size:15px">WHY CHOOSE US</h2>
  <h2 class="abs h-sec" style="left:296px;top:671px;font-size:15px">SERVICES</h2>
  <h2 class="abs h-sec" style="left:501px;top:671px;font-size:15px">OUR MISSION</h2>

  <div class="col-photo" style="left:88px;background:linear-gradient(135deg,#f4ece6,#d8bfae)" role="img" aria-label="Woman relaxing with towel on head"></div>
  <div class="col-photo" style="left:296px;background:linear-gradient(135deg,#fbe0cc,#c89478)" role="img" aria-label="Woman with glowing skin"></div>
  <div class="col-photo" style="left:501px;background:linear-gradient(90deg,#8a6048,#e0d0c0 30%,#c0a070 55%,#8aa040 80%,#6a5030)" role="img" aria-label="Strip of spa and beauty treatment photos"></div>

  <p class="col-text" style="left:88px;text-align:justify">Ut tristique tellus eu faucibus aliquet. Duis venenatis ultrices lorem ac elementum. Ut laoreet leo sed dapibus mattis. Nulla ac egestas ante. Cras sit amet purus adipiscing, egestas ligula nec, suscipit arcu. Suspendisse sed rutrum risus.</p>
  <ul class="col-text checks" style="left:296px">
    <li>Sui blanditiistes es praetiuptatum</li>
    <li>Welenitimos atquqdolores etres</li>
    <li>Euamolestiasexceuri sint timilique</li>
    <li>Suincupaqui officia deserunt</li>
  </ul>
  <div class="col-text" style="left:501px;top:820px"><strong style="color:#222;font-weight:600">Sui blanditiistes es praetiuptatum</strong><br>Eenitimos atquqdolores etres quamolestiasex ceuri sint piditaprdentimilique suincupaqui officia deserunt.</div>

  <div class="more" style="left:88px">More</div>
  <div class="more" style="left:296px">More</div>
  <div class="more" style="left:501px">More</div>
</section>

<section>
  <h2 class="abs h-links">OUR LINKS:</h2>
  <div class="card" style="left:88px;background:linear-gradient(160deg,#f0e4e8,#c89078)" role="img" aria-label="Job search: smiling woman with orchids">
    <div class="card-band"></div><div class="card-title">JOB<br>SEARCH</div>
  </div>
  <div class="card" style="left:240px;background:linear-gradient(160deg,#d8a888,#8a5838)" role="img" aria-label="Business classifieds: spa client with flowers">
    <div class="card-band"></div><div class="card-title">BUSINESS<br>CLASSIFIEDS</div>
  </div>
  <div class="card" style="left:390px;background:linear-gradient(160deg,#f4e4d8,#c08a6a)" role="img" aria-label="Freelancer classifieds: makeup brushes and powder">
    <div class="card-band"></div><div class="card-title">FREELANCER<br>CLASSIFIEDS</div>
  </div>
  <div class="card" style="left:541px;background:linear-gradient(160deg,#e8d4c4,#9a7058)" role="img" aria-label="Course reviews: close-up of eyes">
    <div class="card-band"></div><div class="card-title">COURSE<br>REVIEWS</div>
  </div>
  <div class="click" style="left:88px">CLICK HERE</div>
  <div class="click" style="left:240px">CLICK HERE</div>
  <div class="click" style="left:390px">CLICK HERE</div>
  <div class="click" style="left:541px">CLICK HERE</div>
</section>

<footer>
  <div class="abs footer"></div>
  <span class="foot-nav" style="left:88px">Home</span>
  <span class="foot-nav" style="left:125px">|</span>
  <span class="foot-nav" style="left:139px">About us</span>
  <span class="foot-nav" style="left:187px">|</span>
  <span class="foot-nav" style="left:201px">Services</span>
  <span class="foot-nav" style="left:248px">|</span>
  <span class="foot-nav" style="left:261px">Gallery</span>
  <span class="foot-nav" style="left:306px">|</span>
  <span class="foot-nav" style="left:325px">Blog</span>
  <span class="foot-nav" style="left:365px">|</span>
  <span class="foot-nav" style="left:380px">Contact us</span>
  <div class="abs copyright">Copyright 2013 www.lumarinovo.com All Rights Reserved.</div>
  <span class="social" style="left:576px" aria-label="Social link"></span>
  <span class="social" style="left:599px" aria-label="Social link"></span>
  <span class="social" style="left:622px" aria-label="Social link"></span>
  <span class="social" style="left:645px" aria-label="Social link"></span>
</footer>

</body>
</html>
```